Every Shelf Set Neatly or ESN Organized needs a business card design. ESN Organized is a professi

We need a business card design that is clean, sharp and conveys a sense of organization. I already have a logo.

Target Market(s)

Families (specifically mothers), small business owners, parents, seniors

Industry/Entity Type

Business

Contact Information for Business Card

My website is www.esnorganized-example.com and my Facebook page is http://www.sociallink-example.com/everyshelfsetneatly. The phone number is 418-552-7094 and I want to be listed as Lorna M. Pelham, Owner

Requirements
Must have
• My logo.

```html
<!DOCTYPE html>
<html lang="en">
<head>
<meta charset="utf-8">
<title>ESN Organized – Business Card</title>
<link rel="stylesheet" href="https://fonts.googleapis.com/css2?family=Montserrat:wght@300;400;500;600&display=swap">
<style>
  :root {
    --page-bg: #d8dce1;
    --blue-light: #2f6fd0;
    --blue-mid: #1f55b5;
    --blue-deep: #123a86;
    --chevron-black: #111318;
    --card-light: #f1f3f5;
    --card-light-edge: #dfe3e8;
    --text-white: #ffffff;
    --text-soft: #e3ebf8;
    --brand-navy: #1d3c7a;
  }
  html, body {
    margin: 0;
    padding: 0;
    width: 1200px;
    height: 969px;
    overflow: hidden;
    background: var(--page-bg);
    font-family: "Montserrat", Arial, sans-serif;
  }
  .business-card {
    position: absolute;
    left: 75px;
    top: 184px;
    width: 1050px;
    height: 600px;
    box-shadow: 0 12px 34px rgba(0, 0, 0, 0.18);
    overflow: hidden;
  }
  .card-shapes {
    position: absolute;
    inset: 0;
  }
  .owner-name {
    position: absolute;
    left: 63px;
    top: 58px;
    margin: 0;
    font-size: 36px;
    font-weight: 600;
    color: var(--text-white);
    letter-spacing: 0.3px;
  }
  .owner-title {
    position: absolute;
    left: 63px;
    top: 104px;
    margin: 0;
    font-size: 29px;
    font-weight: 300;
    color: var(--text-soft);
  }
  .contact-list {
    position: absolute;
    left: 63px;
    top: 430px;
    margin: 0;
    padding: 0;
    list-style: none;
    color: var(--text-soft);
  }
  .contact-list li {
    height: 41px;
    font-size: 26px;
    font-weight: 300;
    display: flex;
    align-items: center;
  }
  .contact-list .contact-phone {
    font-weight: 600;
    font-size: 28px;
    color: var(--text-white);
    letter-spacing: 0.5px;
  }
  .social-square {
    display: inline-block;
    width: 22px;
    height: 22px;
    background: var(--text-soft);
    margin-right: 8px;
  }
  .brand-name {
    position: absolute;
    left: 500px;
    top: 262px;
    width: 500px;
    margin: 0;
    font-size: 52px;
    font-weight: 500;
    color: var(--brand-navy);
    letter-spacing: 1px;
    white-space: nowrap;
  }
</style>
</head>
<body>
  <main class="business-card">
    <svg class="card-shapes" width="1050" height="600" viewBox="0 0 1050 600" aria-hidden="true">
      <defs>
        <linearGradient id="blueGradient" x1="0" y1="0" x2="1" y2="0.3">
          <stop offset="0" stop-color="var(--blue-light)"/>
          <stop offset="0.55" stop-color="var(--blue-mid)"/>
          <stop offset="1" stop-color="var(--blue-deep)"/>
        </linearGradient>
        <linearGradient id="lightGradient" x1="0" y1="0" x2="1" y2="1">
          <stop offset="0" stop-color="var(--card-light)"/>
          <stop offset="1" stop-color="var(--card-light-edge)"/>
        </linearGradient>
      </defs>
      <rect class="light-side" width="1050" height="600" fill="url(#lightGradient)"/>
      <polygon class="chevron-stripe" points="631,0 397,298 631,600 427,298" fill="var(--chevron-black)"/>
      <polygon class="blue-panel" points="0,0 631,0 397,298 631,600 0,600" fill="url(#blueGradient)"/>
    </svg>

    <h1 class="owner-name">Lorna M. Pelham</h1>
    <p class="owner-title">Owner</p>

    <ul class="contact-list">
      <li class="contact-phone">P : 418-552-7094</li>
      <li class="contact-web">www.esnorganized-example.com</li>
      <li class="contact-social"><span class="social-square"></span>/everyshelfsetneatly</li>
    </ul>

    <p class="brand-name">ESN Organized</p>
  </main>
</body>
</html>
```